Business card for marketing analytics company

Need a business card for new company. I have a logo already that I want to be built into the card and should use those colours

Company is called steered by tallies
Design must bring steered by tallies to life not be a card that could be for anyone with a logo put on it.

Like the front to be fairly clean and uncluttered bringing the logo out with a suitable design on the back of the card.

The logo represents a compass and business growth so those themes along with numbers, analytics , data are appropriate.
I'm often working with creative industries so also needs to reflect the creative side of analytics rather than be very corporate looking.

Target Market(s)

Ad agency, media agency, consumer goods clients

Industry/Entity Type

Market Research

Contact Information for Business Card

Needs to include name, title, email and phone number

Colors
f78f20
f68d4d
ec1f27

Requirements
Must have
• Must bring steered by tallies to life not be a card that could be for anyone with a logo put on it.
• Logo, Correct colours
• Like a design on the back that relates to company name
• Designs for both sides
Should not have
• Please do not just submit logo and a coloured card.
• It needs to have a design element to it
• No black background
• No clear cards - needs front & back

```html
<!DOCTYPE html>
<html lang="en">
<head>
<meta charset="utf-8">
<title>Steered by Tallies — Business Card</title>
<link rel="stylesheet" href="https://fonts.googleapis.com/css2?family=Montserrat:wght@500&family=Source+Sans+3:wght@400;600&display=swap">
<style>
  :root {
    --page: #eeebe8;
    --card-red: #c11f27;
    --card-orange: #f47321;
    --card-white: #ffffff;
    --ink-white: #ffffff;
    --slate: #4a5560;
    --brand-red: #ec1f27;
  }
  * { margin: 0; padding: 0; box-sizing: border-box; }
  html, body { width: 1200px; height: 900px; overflow: hidden; }
  body {
    position: relative;
    background: var(--page);
    font-family: "Source Sans 3", "Helvetica Neue", Arial, sans-serif;
  }

  .card { position: absolute; overflow: hidden; }

  /* Back: red side with contact details */
  .card-back {
    left: 78px; top: 35px; width: 587px; height: 362px;
    background: var(--card-red);
  }
  .card-back .accent-band {
    position: absolute; left: 0; top: 0; width: 100px; height: 100%;
    background: var(--card-orange);
  }
  .card-back .brand-ring {
    position: absolute; left: 45px; top: 10px; width: 320px; height: 320px;
    border: 9px solid var(--ink-white); border-radius: 50%;
  }
  .card-back .brand-name {
    position: absolute; left: 95px; top: 128px; width: 220px;
    color: var(--ink-white); font-weight: 600; font-size: 30px; line-height: 1.15;
    text-align: center;
  }
  .contact {
    position: absolute; right: 30px; top: 120px; text-align: right;
    color: var(--ink-white);
  }
  .contact .person-name { font-weight: 600; font-size: 19px; letter-spacing: 0.2px; line-height: 1.1; }
  .contact .person-title { font-size: 15px; line-height: 1.2; }
  .contact .lines { margin-top: 32px; font-size: 15px; line-height: 22px; }
  .contact .line { display: flex; justify-content: flex-end; align-items: center; gap: 7px; }
  .contact svg { width: 13px; height: 13px; fill: var(--ink-white); }

  /* Front: white side with wordmark */
  .card-front {
    left: 388px; top: 505px; width: 567px; height: 352px;
    background: var(--card-white);
  }
  .wordmark {
    position: absolute; left: 90px; top: 105px;
    display: flex; align-items: center; gap: 26px;
  }
  .wordmark .mark-circle {
    width: 118px; height: 118px; border-radius: 50%;
    border: 6px solid var(--brand-red);
  }
  .wordmark .name {
    font-family: "Montserrat", "Helvetica Neue", Arial, sans-serif;
    font-weight: 500; font-size: 34px; line-height: 1.1; color: var(--slate);
  }
</style>
</head>
<body>
  <section class="card card-back">
    <div class="accent-band"></div>
    <div class="brand-ring"></div>
    <div class="brand-name">Steered by Tallies</div>
    <div class="contact">
      <div class="person-name">MARCUS HALE</div>
      <div class="person-title">Managing Director</div>
      <div class="lines">
        <div class="line">(044)987650123
          <svg viewBox="0 0 24 24" aria-hidden="true"><path d="M6.6 10.8a15.1 15.1 0 0 0 6.6 6.6l2.2-2.2a1 1 0 0 1 1-.25 11.4 11.4 0 0 0 3.6.57 1 1 0 0 1 1 1V20a1 1 0 0 1-1 1A17 17 0 0 1 3 4a1 1 0 0 1 1-1h3.5a1 1 0 0 1 1 1c0 1.25.2 2.45.57 3.6a1 1 0 0 1-.25 1z"/></svg>
        </div>
        <div class="line">hello@steeredmail.com
          <svg viewBox="0 0 24 24" aria-hidden="true"><path d="M2 5h20v14H2z M3.5 6.5 12 13l8.5-6.5v-.1H3.5z" fill-rule="evenodd"/></svg>
        </div>
      </div>
    </div>
  </section>

  <section class="card card-front">
    <div class="wordmark">
      <div class="mark-circle"></div>
      <div class="name">Steered by<br>Tallies</div>
    </div>
  </section>
</body>
</html>
```